E-Book-Cover für Ratgeber zum Thema Weisheit
Zielgruppe
Ich bin ein experimenteller Schriftsteller, der ein E-Book über Quellbuch Verlagsdienst auf Buchora veröffentlichen möchte. Das Thema des Ratgebers ist Weisheit.
Weisheit gilt als ein eher antiquierter und abstrakter Begriff. Das ist ein Irrtum. Sie ist wichtiger als je zuvor und kann beschrieben werden. Weder ist sie gleichzusetzen mit Klugheit, noch mit spiritueller Erleuchtung. Sie beinhaltet bestimmte Eigenschaften wie Vernunft, Wissbegierde, Demut, Einfühlungsvermögen, Intuition, Auflehnung... Wobei rationales Denken das oberste Gebot ist. Es wird u.a. gezeigt, was Weisheit für das eigene Leben bringt und wie man sie anstreben kann.
Die Zielgruppe sind alle Menschen, die an Philosophie, Psychologie, Selbstoptimierung oder Religionen bzw. Atheismus interessiert sind. Menschen, die nach einer Erkenntnis oder 'Erleuchtung' suchen und etwas Besonderes in der Bücherflut entdecken möchten. Es ist weniger für Akademiker geschrieben; eher für die 'normale', durchschnittliche Bevölkerung und kann auch von bildungsferneren Schichten aller Altersgruppen verstanden werden.
Meine Vermutung ist, dass es bei offenen Personen mittleren Alters Anklang finden könnte.
Aufgabenstellung
Der Titel und der Untertitel des Buches müssen vorkommen (Titel: 'Der Klare Blick'; Untertitel: 'Wie Sie mit dem revolutionären Konzept der modernen Weisheit wahre Größe erlangen'). Außerdem soll ein runder Button/Aufkleber/Sticker auf dem Cover kleben, welcher folgenden Text enthält: 'Mit Selbsttest! Wie weise bin ich?').
Natürlich soll der Name des Autors ebenfalls vorkommen: 'Malte Ruhland'
Das Cover soll sehr aus der Masse herausstechen, demnach ein echter Hingucker sein. Der potenzielle Kunde soll sofort neugierig sein! Es muss sowohl klein (als Thumbnail und am Smartphone), als auch groß gut aussehen und der Titel stets gut lesbar sein. Außerdem muss es schwarzweiß gut aussehen und erkennbar sein (für ebook-reader).
Buchora gibt folgende Werte für die Bilddatei vor: Die idealen Abmessungen für Coverdateien liegen bei 2 560 x 1 600 Pixeln. Mindestens 300 dpi. Die Größe der Bilddatei sollte 50MB nicht übersteigen. Farbprofil: RGB. DATEIFORMAT: JPG oder TIFF
Coverbilder mit weißem oder sehr hellem Hintergrund heben sich kaum vom Hintergrund ab. Fügen Sie einen dünnen Rahmen (3–4 Pixel) in Mittelgrau hinzu, um die Ränder des Coverbilds besser sichtbar zu machen.
Welches Cover gut zum Thema Weisheit passt, überlasse ich Ihrer Genialität. Ich dachte vielleicht an eine Art Blitz, Supernova, Erleuchtung, Explosion, geometrische Form o.ä. Aber Sie können sich etwas ganz eigenes ausdenken. Es sollte eher abstrakt sein. Außerdem muss es klar, edel und modern wirken, weniger comichaft oder verspielt/kitschig. Es darf etwas aggressiv bzw. 'revolutionär' wirken.

```html
<!DOCTYPE html>
<html lang="de">
<head>
<meta charset="utf-8">
<title>Der Klare Blick – Malte Ruhland</title>
<link rel="stylesheet" href="https://fonts.googleapis.com/css2?family=Orbitron:wght@500;700&family=Carlito:wght@700&display=swap">
<style>
  :root {
    --night: #0d1226;
    --navy: #141b33;
    --lavender: #8e8fbf;
    --mist: #5b5e8a;
    --white: #ffffff;
    --band: rgba(120, 124, 150, 0.82);
  }
  html, body {
    margin: 0;
    padding: 0;
    overflow: hidden;
    background: var(--night);
  }
  .cover {
    position: relative;
    width: 750px;
    height: 1200px;
    overflow: hidden;
    background: linear-gradient(180deg, #0b0f1f 0%, var(--navy) 45%, #1a1f3a 100%);
    color: var(--white);
  }
  .scene {
    position: absolute;
    left: 0;
    top: 510px;
    width: 750px;
    height: 690px;
  }
  .author {
    position: absolute;
    top: 34px;
    left: 0;
    width: 100%;
    text-align: center;
    font-family: "Orbitron", sans-serif;
    font-weight: 500;
    font-size: 38px;
    letter-spacing: 2px;
    margin: 0;
  }
  .title {
    position: absolute;
    top: 100px;
    left: 0;
    width: 100%;
    margin: 0;
    text-align: center;
    font-family: "Orbitron", sans-serif;
    font-weight: 700;
    font-size: 104px;
    line-height: 140px;
    letter-spacing: 4px;
  }
  .title span { display: block; }
  .subtitle {
    position: absolute;
    top: 384px;
    left: 0;
    width: 100%;
    margin: 0;
    text-align: center;
    font-family: "Carlito", sans-serif;
    font-weight: 700;
    font-size: 33px;
    line-height: 42px;
  }
  .sticker {
    position: absolute;
    left: 0;
    top: 1022px;
    width: 332px;
    height: 116px;
  }
  .sticker svg { position: absolute; inset: 0; }
  .sticker-text {
    position: absolute;
    left: 0;
    top: 14px;
    width: 296px;
    text-align: center;
    font-family: "Carlito", sans-serif;
    font-weight: 700;
    font-size: 31px;
    line-height: 44px;
    margin: 0;
  }
</style>
</head>
<body>
<main class="cover">
  <svg class="scene" viewBox="0 0 750 690" role="img" aria-label="Illustration: Reihen grauer Figuren, in der Mitte eine hell leuchtende Figur mit erhobenen Armen">
    <defs>
      <linearGradient id="crowd" x1="0" y1="0" x2="0" y2="1">
        <stop offset="0" stop-color="#141b33" stop-opacity="0"/>
        <stop offset="0.2" stop-color="#4e5078"/>
        <stop offset="0.55" stop-color="#7d7ea9"/>
        <stop offset="1" stop-color="#2a3050"/>
      </linearGradient>
      <radialGradient id="glow" cx="0.5" cy="0.62" r="0.45">
        <stop offset="0" stop-color="#ffffff"/>
        <stop offset="0.35" stop-color="#d9dcf2" stop-opacity="0.7"/>
        <stop offset="1" stop-color="#8e8fbf" stop-opacity="0"/>
      </radialGradient>
    </defs>
    <rect width="750" height="690" fill="url(#crowd)"/>
    <rect width="750" height="690" fill="url(#glow)"/>
  </svg>

  <p class="author">MALTE RUHLAND</p>
  <h1 class="title"><span>DER KLARE</span><span>BLICK</span></h1>
  <p class="subtitle">Wie Sie mit dem revolutionären Konzept<br>der modernen Weisheit<br>wahre Größe erlangen</p>

  <div class="sticker">
    <svg viewBox="0 0 332 116" width="332" height="116" aria-hidden="true">
      <polygon points="0,0 283,0 332,116 0,116" fill="var(--band)"/>
    </svg>
    <p class="sticker-text">Mit Selbsttest!<br>Wie weise bin ich?</p>
  </div>
</main>
</body>
</html>
```